Bright Net Rally Website Design (design layout only)

We need a website design for a new nonprofit organization based in Des Moines, Iowa called Bright Net Rally. The nonprofit provides soccer training opportunities to youth soccer players looking to improve their game while also affecting the lives of the less fortunate in a positive way. While participating in the training programs the players also go out and raise money for selected charities. The organization then donates the funds. In its first 18 months we donated $10,500. We would like to see designs attempt to symbolize the mission of the nonprofit - essentially "improve you while improving someone else."

We would like to see the following features:

· A place to donate - Our intent is to have the home page linked to the donation page; a simple straight-forward process for people to give money, and make donating as painless as possible - no account needed to make a donation, credit card or e-check should be the only information needed to donate, and have it be on a single page.

· A photo gallery so people can browse the photo gallery to get a better understanding of our organization and a place to add videos and a calendar to show upcoming events

· A place for contact information and the profiles of directors and board members. This should include a spot showing all the charities the organization donates to. Also includes a news section/blog for comments and suggestions.

We want the design to revolve around the content and mission. We would really like to stress our organization as nonprofit. We would also like if the website was user friendly and easy to navigate.

The logo of our organization is uploaded

```html
<!DOCTYPE html>
<html lang="en">
<head>
<meta charset="utf-8">
<title>Bright Net Rally</title>
<link rel="stylesheet" href="https://fonts.googleapis.com/css2?family=Open+Sans:wght@300;400;600;700&family=Montserrat:wght@800;900&display=swap">
<style>
  :root {
    --page: #ebebeb;
    --header: rgba(214, 214, 214, 0.95);
    --nav-text: #2a2a2a;
    --brand-green: #7f9e4c;
    --hero-dark: #0b0f0b;
    --hero-grass: #3f7a2a;
    --tagline-box: rgba(12, 40, 12, 0.6);
    --orange: #d04a27;
    --orange-light: #d85b3b;
    --white: #ffffff;
    --ink: #111111;
    --muted: #555555;
    --faint: #a8a8a8;
    --link: #2a9fd8;
    --thumb: #29a3dc;
    --date-top: #ececec;
    --date-bottom: #c9c9c9;
    --rule: #bdbdbd;
  }
  * { box-sizing: border-box; margin: 0; padding: 0; }
  html, body { width: 960px; height: 1200px; overflow: hidden; }
  body {
    position: relative;
    background: var(--page);
    font-family: "Open Sans", Arial, sans-serif;
    color: var(--ink);
  }

  /* Hero */
  .hero-photo {
    position: absolute; left: 0; top: 0; width: 960px; height: 444px;
    background: linear-gradient(180deg, var(--hero-dark) 0%, #101810 55%, #2c5a20 75%, var(--hero-grass) 100%);
  }
  .site-header {
    position: absolute; left: 0; top: 0; width: 960px; height: 68px;
    background: var(--header);
  }
  .brand-disc {
    position: absolute; left: 92px; top: -7px; width: 152px; height: 152px;
    border-radius: 50%; background: var(--header);
    display: flex; flex-direction: column; align-items: center; justify-content: center;
    padding-top: 18px;
  }
  .brand-name {
    font-weight: 700; font-size: 17px; line-height: 19px; color: var(--brand-green);
    text-align: center;
  }
  .brand-mark {
    width: 14px; height: 14px; border-radius: 50%; background: var(--brand-green);
    margin-bottom: 6px;
  }
  .main-nav {
    position: absolute; right: 90px; top: 24px;
    display: flex; gap: 22px;
  }
  .main-nav a {
    font-size: 14.4px; color: var(--nav-text); text-decoration: none; letter-spacing: 0.2px;
  }
  .tagline {
    position: absolute; left: 156px; top: 193px; width: 302px; height: 168px;
    background: var(--tagline-box); color: var(--white);
    padding: 12px 0 0 12px;
  }
  .tagline .strong {
    display: block; font-family: "Montserrat", Arial, sans-serif; font-weight: 900;
    font-size: 27px; letter-spacing: 3px; line-height: 36px;
  }
  .tagline .soft {
    display: block; font-weight: 400; font-size: 28px; line-height: 36px;
  }

  /* Donation strip */
  .donation-strip {
    position: absolute; left: 90px; top: 474px; width: 780px; height: 94px;
    background: var(--orange); color: var(--white); display: flex;
  }
  .stat {
    width: 140px; background: var(--orange-light);
    display: flex; flex-direction: column; align-items: center; justify-content: center;
  }
  .stat.more { width: 138px; margin-left: auto; }
  .stat-label { font-size: 11px; line-height: 12px; }
  .stat-value { font-family: "Montserrat", Arial, sans-serif; font-weight: 800; font-size: 17px; letter-spacing: 0.5px; }
  .donation-copy { padding: 14px 0 0 38px; width: 300px; }
  .donation-copy .kicker { font-size: 11px; }
  .donation-copy h2 {
    font-family: "Montserrat", Arial, sans-serif; font-weight: 800; font-size: 17px;
    letter-spacing: 1px; line-height: 22px; margin-top: 2px;
  }
  .donation-copy p { font-size: 8px; line-height: 12px; }
  .donate-button {
    position: absolute; left: 468px; top: 32px; width: 133px; height: 32px;
    background: var(--white); color: var(--ink); font-size: 11px;
    display: flex; align-items: center; justify-content: center; text-decoration: none;
  }

  /* Content panel */
  .content-panel {
    position: absolute; left: 90px; top: 600px; width: 780px; height: 416px;
    background: var(--white);
  }
  .section-title {
    position: absolute; top: 32px;
    font-family: "Montserrat", Arial, sans-serif; font-weight: 800; font-size: 13.5px; letter-spacing: 0.5px;
    padding-bottom: 8px; border-bottom: 1px dashed #777;
  }
  .events-title { left: 29px; width: 339px; }
  .blog-title { left: 428px; width: 323px; }
  .column-divider {
    position: absolute; left: 388px; top: 82px; width: 1px; height: 292px; background: #9a9a9a;
  }

  .event { position: absolute; left: 28px; width: 341px; height: 66px; border-bottom: 1px solid var(--rule); }
  .event-date { position: absolute; left: 0; top: 0; width: 42px; }
  .event-day { height: 36px; background: var(--date-top); font-size: 8.5px; font-weight: 600; display: flex; align-items: center; justify-content: center; }
  .event-year { height: 10px; background: var(--date-bottom); font-size: 7.5px; display: flex; align-items: center; justify-content: center; }
  .event-title { position: absolute; left: 52px; top: 0; font-size: 11.5px; line-height: 15px; }
  .event-text { position: absolute; left: 52px; top: 22px; width: 290px; font-size: 8px; line-height: 12px; color: var(--muted); }
  .event-meta { position: absolute; left: 0; top: 54px; width: 100%; font-size: 8px; color: var(--muted); }
  .event-meta .time { color: var(--faint); margin-left: 3px; }
  .event-meta .by { position: absolute; left: 50px; }
  .event-meta .details { position: absolute; right: 0; color: var(--link); }

  .post { position: absolute; top: 82px; width: 141px; }
  .post-thumb { width: 141px; height: 90px; background: var(--thumb); }
  .post-title { font-size: 11.5px; line-height: 15px; margin-top: 8px; }
  .post-meta { font-size: 7px; color: var(--faint); border-top: 1px solid var(--rule); margin-top: 1px; padding-top: 1px; }
  .post-meta .cat { color: var(--link); }
  .post-text { font-size: 8.2px; line-height: 11.9px; margin-top: 13px; }
  .post-more { display: block; text-align: right; font-size: 8.5px; color: var(--link); margin-top: 9px; text-decoration: none; }
</style>
</head>
<body>

<div class="hero-photo" role="img" aria-label="Photo of a youth player dribbling a soccer ball between orange training cones on a floodlit grass pitch"></div>

<header class="site-header">
  <nav class="main-nav">
    <a href="#">HOME</a>
    <a href="#">ABOUT US</a>
    <a href="#">DONATE</a>
    <a href="#">GALLERY</a>
    <a href="#">EVENTS</a>
    <a href="#">CONTACT US</a>
  </nav>
</header>

<div class="brand-disc">
  <span class="brand-mark"></span>
  <span class="brand-name">Bright Net<br>Rally</span>
</div>

<div class="tagline">
  <span class="strong">IMPROVE</span>
  <span class="soft">you while</span>
  <span class="strong">IMPROVING</span>
  <span class="soft">someone else</span>
</div>

<section class="donation-strip">
  <div class="stat">
    <span class="stat-label">Our Goal</span>
    <span class="stat-value">$20,000</span>
  </div>
  <div class="donation-copy">
    <span class="kicker">Give Us</span>
    <h2>DONATION</h2>
    <p>Lorem Ipsum has been the industry's standard<br>dummy text ever since the 1500s.</p>
  </div>
  <a class="donate-button" href="#">Donate Now!</a>
  <div class="stat more">
    <span class="stat-label">More Needed</span>
    <span class="stat-value">$10,000</span>
  </div>
</section>

<main class="content-panel">
  <h3 class="section-title events-title">UPCOMING EVENTS</h3>
  <h3 class="section-title blog-title">BLOG POSTS</h3>
  <div class="column-divider"></div>

  <article class="event" style="top:82px">
    <div class="event-date"><div class="event-day">8 Aug</div><div class="event-year">2014</div></div>
    <div class="event-title">Lorem Ipsum is simply dummy text of the printing</div>
    <p class="event-text">It is a long established fact that a reader will be distracted by the readable content of a page when looking at its layout.</p>
    <div class="event-meta"><span class="time">12:00 AM</span><span class="by">By: Lorem Ipsum</span><span class="details">Details</span></div>
  </article>
  <article class="event" style="top:157px">
    <div class="event-date"><div class="event-day">8 Aug</div><div class="event-year">2014</div></div>
    <div class="event-title">Lorem Ipsum is simply dummy text of the printing</div>
    <p class="event-text">It is a long established fact that a reader will be distracted by the readable content of a page when looking at its layout.</p>
    <div class="event-meta"><span class="time">12:00 AM</span><span class="by">By: Lorem Ipsum</span><span class="details">Details</span></div>
  </article>
  <article class="event" style="top:232px">
    <div class="event-date"><div class="event-day">8 Aug</div><div class="event-year">2014</div></div>
    <div class="event-title">Lorem Ipsum is simply dummy text of the printing</div>
    <p class="event-text">It is a long established fact that a reader will be distracted by the readable content of a page when looking at its layout.</p>
    <div class="event-meta"><span class="time">12:00 AM</span><span class="by">By: Lorem Ipsum</span><span class="details">Details</span></div>
  </article>
  <article class="event" style="top:307px">
    <div class="event-date"><div class="event-day">8 Aug</div><div class="event-year">2014</div></div>
    <div class="event-title">Lorem Ipsum is simply dummy text of the printing</div>
    <p class="event-text">It is a long established fact that a reader will be distracted by the readable content of a page when looking at its layout.</p>
    <div class="event-meta"><span class="time">12:00 AM</span><span class="by">By: Lorem Ipsum</span><span class="details">Details</span></div>
  </article>

  <article class="post" style="left:432px">
    <div class="post-thumb" role="img" aria-label="Blog post image"></div>
    <div class="post-title">Lorem Ipsum is simply text of the printing</div>
    <div class="post-meta"><span class="cat">Soccer</span> / April 7, 2014</div>
    <p class="post-text">It is a long established fact that a reader will be distracted by the readable content of a page when looking at its layout. The point of using Lorem Ipsum is that it has a more-or-less normal distribution of letters, as opposed to using 'Content here, content here', making it look like readable English.</p>
    <a class="post-more" href="#">Read more...</a>
  </article>
  <article class="post" style="left:601px">
    <div class="post-thumb" role="img" aria-label="Blog post image"></div>
    <div class="post-title">Lorem Ipsum is simply text of the printing</div>
    <div class="post-meta"><span class="cat">Soccer</span> / April 7, 2014</div>
    <p class="post-text">It is a long established fact that a reader will be distracted by the readable content of a page when looking at its layout. The point of using Lorem Ipsum is that it has a more-or-less normal distribution of letters, as opposed to using 'Content here, content here', making it look like readable English.</p>
    <a class="post-more" href="#">Read more...</a>
  </article>
</main>

</body>
</html>
```